Flat Belly Design Graphics for Social

I want to create 9 social media graphics (new Instagram size 4:5 (1080 x 1350 pixels) focusing on our Flat Belly Graphics, using the pics attached. Use the attached pics, NO RANDOM STOCK PHOTOGRAPHY. For the color scheme of the graphics, the color palette is attached. YOU MUST POST ALL 9 GRAPHICS IN ONE ENTRY.
Using the 3 titles below, create one set of graphics. 1) with all text, then for the others, use the pictures as detailed below in IMPORTANT:
1. Ten-Week Bright Morning Reboot
2. The Quick Garden Kitchen Menu Guide
3. Studio Habits for Lasting Energy Past Midlife - Zero Gym Needed
IMPORTANT:
Only use RK Pic 1 and RK Pic 2 with the title, Ten-Week Bright Morning Reboot
Only use meal plan1 and meal plan2 pics with the title, Quick Garden Kitchen Menu Guide
Only use studio habits 1 and studio habits 2 pics with the title, Studio Habits for Lasting Energy Past Midlife - Zero Gym Needed
women over 40

```html
<!DOCTYPE html>
<html lang="en">
<head>
<meta charset="utf-8">
<title>Social Graphics Set – Morning Reboot, Studio Habits, Menu Guide</title>
<link rel="stylesheet" href="https://fonts.googleapis.com/css2?family=Oswald:wght@600;700&display=swap">
<style>
  :root{
    --board:#5a5a5a;
    --forest:#2e4b4a;
    --forest-veil:rgba(46,75,74,.88);
    --rose:#e89bb0;
    --blush:#fbdde3;
    --white:#ffffff;
  }
  *{box-sizing:border-box;margin:0;padding:0}
  html,body{width:967px;height:1200px;overflow:hidden;background:var(--board)}
  body{position:relative;font-family:"Oswald",Arial Narrow,sans-serif;font-weight:700}
  .tile{position:absolute;width:295px;height:368px;overflow:hidden}
  .headline{position:absolute;display:flex;flex-direction:column;align-items:center;text-align:center;line-height:.98;white-space:nowrap;text-transform:uppercase}
  .headline span{display:block}
  .photo{position:absolute;inset:0}
  .veil{position:absolute;background:var(--forest-veil)}

  /* row 1 – Ten-Week Bright Morning Reboot */
  .reboot-text{left:13px;top:8px;background:var(--forest)}
  .reboot-text .headline{left:0;right:0;top:34px;gap:6px}
  .reboot-produce-a{left:332px;top:8px}
  .reboot-produce-b{left:655px;top:8px}
  .produce{background:linear-gradient(135deg,#c9472e 0%,#5b6b3a 30%,#3b3733 55%,#e07a4f 75%,#d8b23c 100%)}

  /* row 2 – Studio Habits */
  .habits-text{left:12px;top:415px;background:var(--blush)}
  .habits-text .headline{left:0;right:0;top:22px;gap:4px}
  .habits-duo-a{left:334px;top:415px;background:var(--white)}
  .habits-duo-b{left:657px;top:415px}
  .duo-light{background:linear-gradient(180deg,#f3eeea 0%,#b98a6c 45%,#e9e4e0 100%)}
  .duo-sky{background:linear-gradient(90deg,#67c6da 0%,#d9b8a8 45%,#5b4a44 75%,#67c6da 100%)}

  /* row 3 – Menu Guide */
  .menu-text{left:9px;top:816px;background:var(--rose)}
  .menu-text .headline{left:0;right:0;top:30px;gap:4px}
  .menu-host-a{left:333px;top:816px;background:var(--blush)}
  .menu-host-b{left:657px;top:816px}
  .kitchen{background:linear-gradient(180deg,#5b3a2a 0%,#8a5a3c 55%,#4a2d20 100%)}
  .host{position:absolute;left:20px;right:12px;top:22px;bottom:0;border-radius:60px 60px 0 0;background:linear-gradient(180deg,#2a1e1a 0%,#7a5444 30%,#f4f1ee 55%,#e9e5e2 100%)}

  .pink{color:var(--rose)}
  .blush{color:var(--blush)}
  .forest{color:var(--forest)}
  .white{color:var(--white)}
</style>
</head>
<body>

<!-- Ten-Week Bright Morning Reboot: all text -->
<section class="tile reboot-text">
  <h2 class="headline">
    <span class="pink" style="font-size:54px">Ten-Week</span>
    <span class="pink" style="font-size:74px">Bright</span>
    <span class="blush" style="font-size:50px">Morning</span>
    <span class="blush" style="font-size:60px">Reboot</span>
  </h2>
</section>

<!-- Ten-Week Bright Morning Reboot: produce photo, side panel -->
<section class="tile reboot-produce-a">
  <div class="photo produce" role="img" aria-label="Overhead spread of fresh vegetables, salmon, eggs, lentils and fruit on dark wood"></div>
  <div class="veil" style="left:138px;right:0;top:16px;bottom:0"></div>
  <h2 class="headline" style="left:138px;right:0;top:30px;gap:8px">
    <span class="pink" style="font-size:34px">Ten-Week</span>
    <span class="pink" style="font-size:46px">Bright</span>
    <span class="blush" style="font-size:30px">Morning</span>
    <span class="blush" style="font-size:34px">-Reboot-</span>
  </h2>
</section>

<!-- Ten-Week Bright Morning Reboot: produce photo, centre panel -->
<section class="tile reboot-produce-b">
  <div class="photo produce" role="img" aria-label="Frame of fresh produce, salmon, pork, lentils and fruit around a dark board"></div>
  <div class="veil" style="left:59px;right:59px;top:30px;bottom:0;background:var(--forest)"></div>
  <h2 class="headline" style="left:59px;right:59px;top:44px;gap:8px">
    <span class="blush" style="font-size:38px">Ten-Week</span>
    <span class="blush" style="font-size:54px">Bright</span>
    <span class="pink" style="font-size:34px">Morning</span>
    <span class="pink" style="font-size:38px">-Reboot-</span>
  </h2>
</section>

<!-- Studio Habits: all text -->
<section class="tile habits-text">
  <h2 class="headline">
    <span class="pink" style="font-size:40px">Studio</span>
    <span class="pink" style="font-size:42px">Habits</span>
    <span class="forest" style="font-size:34px">For Lasting</span>
    <span class="forest" style="font-size:58px">Energy</span>
    <span class="forest" style="font-size:40px">Past Midlife</span>
    <span class="forest" style="font-size:34px">Zero Gym</span>
    <span class="forest" style="font-size:40px">Needed</span>
  </h2>
</section>

<!-- Studio Habits: studio habits 1 -->
<section class="tile habits-duo-a">
  <div class="photo duo-light" style="bottom:180px" role="img" aria-label="Studio habits 1: two women sharing a surprised whisper"></div>
  <div class="veil" style="left:0;right:0;top:188px;bottom:0;background:var(--forest)"></div>
  <h2 class="headline" style="left:0;right:0;top:186px;gap:8px">
    <span class="pink" style="font-size:30px">Studio Habits</span>
    <span class="white" style="font-size:32px">For Lasting Energy</span>
    <span class="blush" style="font-size:54px">Past Midlife</span>
    <span class="blush" style="font-size:24px">Zero Gym Needed</span>
  </h2>
</section>

<!-- Studio Habits: studio habits 2 -->
<section class="tile habits-duo-b">
  <div class="photo duo-sky" role="img" aria-label="Studio habits 2: excited woman against a sky-blue backdrop with a friend whispering"></div>
  <div class="veil" style="left:118px;right:0;top:32px;bottom:36px"></div>
  <h2 class="headline" style="left:124px;right:6px;top:44px;gap:4px">
    <span class="pink" style="font-size:30px">Studio</span>
    <span class="pink" style="font-size:38px">Habits</span>
    <span class="blush" style="font-size:30px">For Lasting</span>
    <span class="blush" style="font-size:38px">Energy</span>
    <span class="blush" style="font-size:24px">Past Midlife</span>
    <span class="blush" style="font-size:26px">Zero Gym</span>
    <span class="blush" style="font-size:28px">Needed</span>
  </h2>
</section>

<!-- Menu Guide: all text -->
<section class="tile menu-text">
  <h2 class="headline">
    <span class="forest" style="font-size:40px">The Quick</span>
    <span class="forest" style="font-size:36px">Garden Kitchen</span>
    <span class="blush" style="font-size:100px">Menu</span>
    <span class="blush" style="font-size:96px">Guide</span>
  </h2>
</section>

<!-- Menu Guide: meal plan1 -->
<section class="tile menu-host-a">
  <div class="host" role="img" aria-label="Meal plan1: smiling host in a white sweater pointing down at the title"></div>
  <div class="veil" style="left:83px;right:83px;top:188px;bottom:0;background:linear-gradient(180deg,rgba(46,75,74,0) 0%,var(--forest) 30%)"></div>
  <h2 class="headline" style="left:83px;right:83px;top:196px;gap:4px">
    <span class="forest" style="font-size:22px">The Quick</span>
    <span class="forest" style="font-size:17px">Garden Kitchen</span>
    <span class="pink" style="font-size:54px">Menu</span>
    <span class="pink" style="font-size:52px">Guide</span>
  </h2>
</section>

<!-- Menu Guide: meal plan2 -->
<section class="tile menu-host-b kitchen" role="img" aria-label="Warm wood kitchen interior">
  <div class="host" role="img" aria-label="Meal plan2: smiling host in a white sweater pointing down at the title, in a kitchen"></div>
  <div class="veil" style="left:83px;right:83px;top:188px;bottom:0;background:linear-gradient(180deg,rgba(46,75,74,0) 0%,var(--forest) 30%)"></div>
  <h2 class="headline" style="left:83px;right:83px;top:196px;gap:4px">
    <span class="forest" style="font-size:22px">The Quick</span>
    <span class="forest" style="font-size:17px">Garden Kitchen</span>
    <span class="pink" style="font-size:54px">Menu</span>
    <span class="pink" style="font-size:52px">Guide</span>
  </h2>
</section>

</body>
</html>
```